design a construction company business card

Design business card around our logo. Card must have all the typical info: name, title, address, phone, email, business name, etc. Somewhere on the card I would like to see our motto "Grounded in honesty... Driven by dedication." Consider adding a splash of bright orange to the card to complement the blues and silvers/grays in the logo. We are open to metallic inks, textures, etc. We would like to see options on both light and dark backgrounds. The font in the logo is Euro Technic Extended Regular.

```html
<!DOCTYPE html>
<html lang="en">
<head>
<meta charset="utf-8">
<title>Halden Building, Inc. — Business Card</title>
<link rel="stylesheet" href="https://fonts.googleapis.com/css2?family=Exo+2:wght@300;400;600;700&family=Open+Sans:wght@400&display=swap">
<style>
  :root {
    --page-bg: #e4e4e4;
    --card-white: #ffffff;
    --brand-navy: #28449c;
    --brand-blue: #1479bd;
    --brand-deep: #283b91;
    --text-grey: #4a4a4a;
    --muted-grey: #8a8a8a;
    --rule-grey: #d2d2d2;
  }
  * { box-sizing: border-box; margin: 0; padding: 0; }
  html, body {
    width: 1125px; height: 1200px; overflow: hidden;
    background: var(--page-bg);
    font-family: "Exo 2", sans-serif;
  }
  .card {
    position: absolute;
    left: 171px;
    width: 826px;
    height: 472px;
    overflow: hidden;
  }
  /* ---------- front ---------- */
  .card--front { top: 106px; background: var(--card-white); }
  .front__brand {
    position: absolute; left: 104px; top: 240px; width: 296px;
    text-align: center; color: var(--brand-navy); font-weight: 700;
  }
  .front__brand-name { font-size: 58px; letter-spacing: 6px; line-height: 1; }
  .front__brand-sub { font-size: 20px; letter-spacing: 1px; margin-top: 8px; }
  .front__divider {
    position: absolute; left: 440px; top: 116px; width: 1px; height: 238px;
    background: var(--rule-grey);
  }
  .front__details { position: absolute; left: 481px; top: 124px; color: var(--text-grey); }
  .person__name { font-size: 29px; font-weight: 700; color: var(--brand-navy); line-height: 1.1; }
  .person__title { font-size: 20px; font-weight: 300; color: var(--muted-grey); margin-top: 3px; letter-spacing: .5px; }
  .address { font-size: 19px; line-height: 25px; margin-top: 14px; letter-spacing: .4px; }
  .contact { list-style: none; margin-top: 16px; }
  .contact__item { display: flex; align-items: center; gap: 9px; font-size: 18px; line-height: 26px; letter-spacing: .4px; }
  .contact__item:first-child { font-size: 19px; }
  .contact__icon { width: 18px; height: 18px; flex: none; fill: var(--brand-navy); }
  .front__band-rule {
    position: absolute; left: 0; right: 0; bottom: 17px; height: 2px; background: var(--rule-grey);
  }
  .front__band {
    position: absolute; left: 0; right: 0; bottom: 0; height: 16px;
    background: linear-gradient(90deg, var(--brand-deep), var(--brand-blue) 55%, var(--brand-deep));
  }
  /* ---------- back ---------- */
  .card--back {
    top: 639px;
    background: linear-gradient(180deg, var(--brand-blue) 0%, #2253a8 50%, var(--brand-deep) 100%);
    color: #fff;
  }
  .back__brand {
    position: absolute; right: 58px; bottom: 64px; width: 354px; text-align: center; font-weight: 700;
  }
  .back__brand-name { font-size: 68px; letter-spacing: 8px; line-height: 1; }
  .back__brand-sub { font-size: 23px; letter-spacing: 1px; margin-top: 6px; }
  .back__motto {
    position: absolute; right: 52px; bottom: 34px;
    font-family: "Open Sans", sans-serif; font-size: 17px;
  }
</style>
</head>
<body>
  <section class="card card--front">
    <div class="front__brand">
      <div class="front__brand-name">HALDEN</div>
      <div class="front__brand-sub">BUILDING, INC.</div>
    </div>
    <div class="front__divider"></div>
    <div class="front__details">
      <h1 class="person__name">MARK ELLISON</h1>
      <p class="person__title">CEO/FOUNDER</p>
      <p class="address">4120 Birchwood Court<br>Fairbanks, Alaska 99701</p>
      <ul class="contact">
        <li class="contact__item">
          <svg class="contact__icon" viewBox="0 0 24 24" aria-hidden="true"><path d="M6.6 10.8a15.1 15.1 0 0 0 6.6 6.6l2.2-2.2c.3-.3.7-.4 1-.2 1.1.4 2.3.6 3.6.6.6 0 1 .4 1 1V20c0 .6-.4 1-1 1A17 17 0 0 1 3 4c0-.6.4-1 1-1h3.5c.6 0 1 .4 1 1 0 1.3.2 2.5.6 3.6.1.3 0 .7-.2 1z"/></svg>
          555 210 4867
        </li>
        <li class="contact__item">
          <svg class="contact__icon" viewBox="0 0 24 24" aria-hidden="true"><path d="M3 5h18v14H3zm2 2v.4l7 4.6 7-4.6V7zm0 2.8V17h14V9.8l-7 4.6z"/></svg>
          mark@haldenbuild.com
        </li>
        <li class="contact__item">
          <svg class="contact__icon" viewBox="0 0 24 24" aria-hidden="true"><circle cx="12" cy="12" r="10"/><path d="M8 6c2 1 1 3 3 4s0 3-2 3-2 3-1 5M15 5c-1 2 1 3 3 3M17 14c-2 0-3 2-2 4" stroke="#fff" stroke-width="1.6" fill="none"/></svg>
          www.haldenbuild.com
        </li>
      </ul>
    </div>
    <div class="front__band-rule"></div>
    <div class="front__band"></div>
  </section>

  <section class="card card--back">
    <div class="back__brand">
      <div class="back__brand-name">HALDEN</div>
      <div class="back__brand-sub">BUILDING, INC.</div>
    </div>
    <p class="back__motto">Grounded in honesty... Driven by dedication.</p>
  </section>
</body>
</html>
```